Wordpress Theme for Medical Clinics

** Please view updated Sitemap2.pdf doc to clarify some confusion ***

This is a multiuser WordPress subscription site for medical clinics. Please see attachment for sitemap. Please do not include extra content like social media icons, search bars, or images. If you have questions, please ask for clarification.
The site contains the following pages and sub-pages:

1. Home
2. Our Clinic
2a. Our Clinic > Mission
2b. Our Clinic > Services
2c. Our Clinic > Clinic Policies
2d. Our Clinic > Schedules
3. Our Staff
3a. Our Staff > [Staff member page]
4. Resources
4a. Resources > Patient Health (index)
4b. Resources > Patient Health (index) > [post]
4c. Resources > Links
4d. Resources > Forms
5. Alerts
5a. Alerts > [Alert Page]
6. Contact Us

Includes the Following Pages, Subpages, and Content
1. Home
a. About Us
b. Our Staff
c. Bulletins
d. Accepting New Patients (shown as an alert widget)
e. Links
i. Physician Toolbox
ii. Book an Appointment
f. Clinic Policies
i. Show first 3 policies (e.g. Late Arrivals, Missed Appointments, Fees)
ii. Link to Clinic Policies page
g. Primary widget (displayed on all pages)
i. Hours of operation
ii. Contact Info
1. Tel
2. Fax
3. Email
4. Address
5. Get directions (link to Google Maps)
2. Our Clinic
a. Main Page
i. Clinic Name
ii. Overview
iii. Languages Spoken
iv. Secondary Navigation
1. Mission
2. Services
3. Clinic Policies
4. Schedules (see attachment)
b. Our Clinic > Mission
c. Our Clinic > Services
i. For each service include service TITLE and DESCRIPTION
d. Our Clinic > Clinic Policies
i. For each policy include policy TITLE and DESCRIPTION
ii. Include the following policies in mockup
1. Late arrivals
2. Missed appointments
3. Fees for missed appointments
4. Referrals and follow-ups
5. Services not covered by RDA
6. Information for LTF patients
7. Medical Legal Reports
e. Our Clinic > Schedules
3. Our Staff
a. Main Page
i. Display a list of staff members. Include NAME and DESIGNATION
b. Our Staff > [Staff Name]
i. Include NAME, PICTURE, DESIGNATION, and BIO
4. Resources
a. Resources > Patient Health
i. Main Page
1. Posts (ordered by date)
a. Title
b. Summary
2. Side Navigation
a. Post Categories
ii. Patient Health > [post title]
1. Title
2. Post Category
3. Date
4. Author
5. Summary
6. Body
b. Resources > Links
1. Secondary Navigation - Categories
a. Sample Categories:
i. Local Services
ii. RDA and Drug Coverage
iii. Mental Health Resources
2. Category page
a. Include the following links in the 'Local Services' category
i. Hypertension clinics
ii. Home Care services
iii. Vaccine Clinics
c. Resources > Forms
i. Display a table with form TITLE and CATEGORY
ii. Side Navigation
1. Form Categories
a. Use the following sample Categories
i. Referrals
ii. Insurance
iii. Intake
iv. Discharge
v. Waivers
5. Alerts
a. Main page
i. List of all Alert posts
1. Include post TITLE as a link to the post
ii. Side Navigation
1. Alerts Archive
a. shown as Month + Number of posts
iii. Alerts > [Alert page]
1. Include TITLE, DATE, AUTHOR, BODY
6. Contact Us
a. Map
b. Hours of operation
c. Address
d. Phone number
e. Fax number
e. Fax number
f. Map
g. Email

Design notes:
- fixed width
- responsive (need designs for mobile, tablet, and desktop)
- simple, dark font, white background
- use Font Awesome icons where needed
- user adds own logo

Target Market(s)

Medical Clinics

Industry/Entity Type

Medical

Number of Pages Required

5+ page

Font styles to use
Serif
Sans Serif

Requirements
Must have
• Please keep designs very simple.
• Examples:
• https://www.quolbin.com/install
• http://www.ventrohax.com/company/about-us
• http://brindlequota.org/
• http://www.trosk.com/
Should not have
• Minimal or no use of shadows and gradients

```html
<!DOCTYPE html>
<html lang="en">
<head>
<meta charset="utf-8">
<title>Halden Clinics</title>
<link href="https://fonts.googleapis.com/css2?family=Jost:wght@400;500;600&family=Open+Sans:wght@400;600;700&display=swap" rel="stylesheet">
<style>
:root{
  --navy:#1b3d66;
  --menu:#23415f;
  --cyan:#2aa3dc;
  --btn:#86cff0;
  --yellow:#fcd34a;
  --green:#3bb54a;
  --red:#d4202a;
  --text:#333a42;
  --line:#e6e9ec;
  --card:#f6f7f8;
  --footer:#f2f3f4;
}
*{box-sizing:border-box;margin:0;padding:0}
html,body{width:1200px;height:2624px;overflow:hidden}
body{position:relative;background:#fff;font-family:"Open Sans",Arial,sans-serif;color:var(--text)}
h1,h2,h3,h4{font-family:"Jost",Arial,sans-serif;color:var(--navy);font-weight:500}
.abs{position:absolute}

.site-header{left:0;top:0;width:1200px;height:102px}
.brand{left:112px;top:30px;display:flex;align-items:center;gap:12px;font-family:"Jost",sans-serif;font-weight:600;font-size:34px;color:var(--navy)}
.brand-mark{width:28px;height:28px;background:var(--cyan);border-radius:4px}

.hero{left:0;top:102px;width:1200px;height:563px;background:linear-gradient(90deg,#cfc3b8 0%,#e8ded6 35%,#d9d2cc 60%,#eef0f0 100%)}
.hero-arrow{width:38px;height:38px;border-radius:50%;background:rgba(140,170,200,.85);display:flex;align-items:center;justify-content:center}
.hero-badge{left:455px;top:233px;width:290px;height:290px;border-radius:50%;background:rgba(35,65,95,.88);text-align:center;color:#fff;padding-top:72px}
.hero-badge h1{color:#fff;font-size:34px;font-weight:500;margin-bottom:10px}
.hero-badge p{font-size:11.5px;line-height:18px;width:190px;margin:0 auto 16px}
.btn-yellow{display:inline-block;background:var(--yellow);color:var(--navy);font-size:11.5px;font-weight:700;padding:6px 16px;border-radius:3px;letter-spacing:.2px}

.main-menu{left:880px;top:25px;width:208px;height:302px;background:var(--menu);border-radius:5px;color:#fff;padding:18px 16px}
.menu-head{display:flex;justify-content:space-between;align-items:center;font-family:"Jost",sans-serif;font-size:14px;font-weight:500;margin-bottom:34px}
.main-menu ul{list-style:none}
.main-menu li{font-family:"Jost",sans-serif;font-size:15px;height:41px;display:flex;align-items:center;gap:22px}
.main-menu li::before{content:"›";font-size:16px}

.section-title{font-size:25px}
.rule{height:1px;background:var(--line)}

.availability{left:852px;top:733px;display:flex;align-items:center;gap:12px;font-size:9px}
.pill{display:flex;align-items:center;gap:6px;border:1px solid #cfd4d8;border-radius:14px;padding:3px 10px;font-size:13px}
.dot{width:7px;height:7px;border-radius:50%;display:inline-block;margin-right:3px}

.cards{left:112px;top:822px;width:978px;display:flex;gap:27px}
.patient-card{width:224px;height:389px;background:var(--card)}
.patient-photo{height:193px;background:linear-gradient(160deg,#d9d4cf,#b8b0a8)}
.patient-body{padding:14px 10px}
.patient-body h3{font-size:15px;font-weight:600;margin-bottom:12px}
.patient-body p{font-size:10.5px;line-height:17.5px;margin-bottom:14px}
.btn-blue{display:inline-block;background:var(--btn);color:var(--navy);font-size:10.5px;padding:3px 10px}

.about{left:110px;top:1290px;width:980px;text-align:center}
.about p{font-size:10.5px;line-height:19px;margin-top:24px}

.alerts-title{left:114px;top:1520px}
.carousel-ctrl{left:1068px;top:1528px;font-size:14px;color:#999}
.alerts{left:112px;top:1603px;width:980px;display:flex;gap:0}
.alert{width:334px;display:flex;gap:16px}
.date{width:44px;height:46px;background:var(--green);color:#fff;font-size:10px;font-weight:700;text-align:center;line-height:13px;padding-top:4px;flex:none}
.alert h4{font-family:"Open Sans",sans-serif;font-size:11px;font-weight:700;line-height:19px;color:var(--navy)}
.alert p{font-size:11px;line-height:19px;color:#3a5f85}

.staff-title{left:0;top:1752px;width:1200px;text-align:center}
.staff{left:110px;top:1866px;width:980px;display:flex;gap:27px}
.member{width:224px}
.member .label{font-family:"Jost",sans-serif;font-size:14px;font-weight:600;color:var(--navy)}
.member h3{font-size:20px;color:var(--cyan);line-height:26px}
.member .role{font-size:10px;font-weight:700;color:var(--navy);margin-bottom:22px}
.member p{font-size:10.5px;line-height:17.5px;margin-bottom:18px}
.member .btn-blue{padding:3px 20px}
.view-all{left:534px;top:2136px}

.toolbox{left:115px;top:2252px;width:970px;height:212px;background:var(--card);display:flex}
.toolbox-photo{width:310px;height:212px;background:linear-gradient(135deg,#c9d8e6,#7ea6cf)}
.toolbox-body{padding:52px 24px}
.toolbox-body h2{font-size:30px;margin-bottom:10px}
.toolbox-body p{font-size:10.5px;line-height:19px;margin-bottom:14px;width:520px}

.site-footer{left:0;top:2522px;width:1200px;height:102px;background:var(--footer);text-align:center;font-family:"Jost",sans-serif;font-weight:600;font-size:14px;color:#222}
.site-footer nav{margin-top:32px;word-spacing:4px}
.site-footer nav span{margin:0 14px}
.site-footer p{margin-top:10px}
</style>
</head>
<body>

<header class="site-header abs">
  <div class="brand abs"><span class="brand-mark"></span>Halden Clinics</div>
</header>

<section class="hero abs" role="img" aria-label="Photo of a smiling young doctor with a stethoscope beside an older patient">
</section>
<div class="hero-arrow abs" style="left:58px;top:363px"><svg width="12" height="16" viewBox="0 0 12 16"><path d="M9 2 3 8l6 6" stroke="#fff" stroke-width="2.5" fill="none"/></svg></div>
<div class="hero-arrow abs" style="left:1100px;top:363px"><svg width="12" height="16" viewBox="0 0 12 16"><path d="M3 2l6 6-6 6" stroke="#fff" stroke-width="2.5" fill="none"/></svg></div>
<div class="hero-badge abs">
  <h1>Halden Clinics</h1>
  <p>Lorem Ipsum is simply dummy text of the printing and typesetting industry. Lorem Ipsum has been the industry's standard dummy text ever</p>
  <span class="btn-yellow">BOOK AN APPOINTMENT</span>
</div>

<nav class="main-menu abs">
  <div class="menu-head">Menu
    <svg width="18" height="14" viewBox="0 0 18 14"><rect y="0" width="18" height="2.5" fill="#2aa3dc"/><rect y="5.7" width="18" height="2.5" fill="#2aa3dc"/><rect y="11.4" width="18" height="2.5" fill="#2aa3dc"/></svg>
  </div>
  <ul><li>Home</li><li>Clinic</li><li>Our Staff</li><li>Resources</li><li>Contact Us</li></ul>
</nav>

<h2 class="section-title abs" style="left:110px;top:728px">New Patients</h2>
<div class="availability abs">
  <span class="pill"><span class="dot" style="background:var(--green);width:11px;height:11px"></span>Available</span>
  <span><span class="dot" style="background:var(--green)"></span>Accepting</span>
  <span><span class="dot" style="background:var(--red)"></span>Not Accepting</span>
</div>
<div class="rule abs" style="left:110px;top:778px;width:980px"></div>

<div class="cards abs">
  <article class="patient-card"><div class="patient-photo" role="img" aria-label="Portrait photo of an older woman"></div><div class="patient-body"><h3>Patient 1</h3><p>Lorem Ipsum is simply dummy text of the printing and typesetting industry. Lorem Ipsum has been the industry's standard dummy text ever since the 1500s, when an unknown printer took</p><span class="btn-blue">Read More</span></div></article>
  <article class="patient-card"><div class="patient-photo" style="background:linear-gradient(160deg,#8a6a55,#4a342a)" role="img" aria-label="Portrait photo of a young woman"></div><div class="patient-body"><h3>Patient 1</h3><p>Lorem Ipsum is simply dummy text of the printing and typesetting industry. Lorem Ipsum has been the industry's standard dummy text ever since the 1500s, when an unknown printer took</p><span class="btn-blue">Read More</span></div></article>
  <article class="patient-card"><div class="patient-photo" style="background:linear-gradient(160deg,#d6e8f2,#a9c8dc)" role="img" aria-label="Portrait photo of a senior woman"></div><div class="patient-body"><h3>Patient 1</h3><p>Lorem Ipsum is simply dummy text of the printing and typesetting industry. Lorem Ipsum has been the industry's standard dummy text ever since the 1500s, when an unknown printer took</p><span class="btn-blue">Read More</span></div></article>
  <article class="patient-card"><div class="patient-photo" style="background:linear-gradient(160deg,#e0d8d0,#c49a80)" role="img" aria-label="Portrait photo of a senior man"></div><div class="patient-body"><h3>Patient 1</h3><p>Lorem Ipsum is simply dummy text of the printing and typesetting industry. Lorem Ipsum has been the industry's standard dummy text ever since the 1500s, when an unknown printer took</p><span class="btn-blue">Read More</span></div></article>
</div>

<section class="about abs">
  <h2 class="section-title">About Us</h2>
  <p>Lorem Ipsum is simply dummy text of the printing and typesetting industry. Lorem Ipsum has been the industry's standard dummy text ever since the 1500s, when an unknown printer took a galley of type and scrambled it to make a type specimen book. It has survived not only five centuries, but also the leap into electronic typesetting, remaining essentially unchanged. It was popularised in the 1960s with the release of Letraset sheets containing Lorem Ipsum passages, and more recently with desktop publishing software like Aldus PageMaker including versions of Lorem Ipsum.</p>
  <p style="margin-top:18px">Lorem Ipsum is simply dummy text of the printing and typesetting industry. Lorem Ipsum has been the industry's standard dummy text ever since the 1500s.</p>
</section>

<h2 class="section-title alerts-title abs">Alerts/Bulletins</h2>
<div class="carousel-ctrl abs">‹ ›</div>
<div class="rule abs" style="left:110px;top:1575px;width:980px"></div>
<div class="alerts abs">
  <div class="alert"><div class="date">June<br>6th<br>2015</div><div><h4>Lorem Ipsum is simply dummy text of the printing and typesetting industry.</h4><p>Lorem Ipsum has been the industry's standard dummy text ever since the 1500s</p></div></div>
  <div class="alert"><div class="date">June<br>6th<br>2015</div><div><h4>Lorem Ipsum is simply dummy text of the printing and typesetting industry.</h4><p>Lorem Ipsum has been the industry's standard dummy text ever since the 1500s</p></div></div>
  <div class="alert"><div class="date">June<br>6th<br>2015</div><div><h4>Lorem Ipsum is simply dummy text of the printing and typesetting industry.</h4><p>Lorem Ipsum has been the industry's standard dummy text ever since the 1500s</p></div></div>
</div>

<h2 class="section-title staff-title abs">Staff</h2>
<div class="rule abs" style="left:110px;top:1820px;width:980px"></div>
<div class="staff abs">
  <div class="member"><div class="label">Staff 1</div><h3>Owen Tallis</h3><div class="role">Physician</div><p>Lorem Ipsum is simply dummy text of the printing and typesetting industry. Lorem Ipsum has been the industry's standard dummy text ever since the 1500s, when an unknown printer took</p><span class="btn-blue">More</span></div>
  <div class="member"><div class="label">Staff 1</div><h3>Owen Tallis</h3><div class="role">Physician</div><p>Lorem Ipsum is simply dummy text of the printing and typesetting industry. Lorem Ipsum has been the industry's standard dummy text ever since the 1500s, when an unknown printer took</p><span class="btn-blue">More</span></div>
  <div class="member"><div class="label">Staff 1</div><h3>Owen Tallis</h3><div class="role">Physician</div><p>Lorem Ipsum is simply dummy text of the printing and typesetting industry. Lorem Ipsum has been the industry's standard dummy text ever since the 1500s, when an unknown printer took</p><span class="btn-blue">More</span></div>
  <div class="member"><div class="label">Staff 1</div><h3>Owen Tallis</h3><div class="role">Physician</div><p>Lorem Ipsum is simply dummy text of the printing and typesetting industry. Lorem Ipsum has been the industry's standard dummy text ever since the 1500s, when an unknown printer took</p><span class="btn-blue">More</span></div>
</div>
<span class="btn-yellow view-all abs">VIEW ALL STAFF</span>

<section class="toolbox abs">
  <div class="toolbox-photo" role="img" aria-label="Photo of a smiling nurse in blue scrubs in a clinic"></div>
  <div class="toolbox-body">
    <h2>Physician Toolbox</h2>
    <p>Lorem Ipsum is simply dummy text of the printing and typesetting industry. Lorem Ipsum has been the industry's standard dummy text ever since the 1500s, when an unknown printer took</p>
    <span class="btn-blue">Read More</span>
  </div>
</section>

<footer class="site-footer abs">
  <nav>Home<span>|</span>Clinic<span>|</span>Our Staff<span>|</span>Resources<span>|</span>Contact Us</nav>
  <p>© 2015 Company Name , All Rights Reserved</p>
</footer>

</body>
</html>
```